Health Care Company with Logo Needs Business Cards designed

We are a luxury behavioral health company looking for business cards design we already have a logo and are looking for someone to design a sophisticated luxurious looking business card. Please note that Card design should be captivating just like the logo and also encompass the logo color

Industry/Entity Type

Healthcare

Contact Information for Business Card

Logo,company name, tagline, my name and title, contact details, and physical address

```html
<!DOCTYPE html>
<html lang="en">
<head>
<meta charset="utf-8">
<title>Corvane Behavioral Health – Business Card</title>
<link href="https://fonts.googleapis.com/css2?family=Oswald:wght@500;600&family=Arimo:wght@400;700&display=swap" rel="stylesheet">
<style>
  :root {
    --page-bg: #d9d3ca;
    --card-light: #f4eee3;
    --card-mid: #ece3d3;
    --brand-purple: #5e2180;
    --brand-blue: #0b7fc4;
    --brand-orange: #e5600f;
    --ink: #2b2622;
    --band-dark: #3a1240;
    --band-light: #6b2e9b;
    --band-text: #ecdcd4;
    --band-muted: #b59c80;
  }
  html, body {
    margin: 0;
    width: 1200px;
    height: 927px;
    overflow: hidden;
    background: var(--page-bg);
  }
  .business-card {
    position: absolute;
    left: 60px;
    top: 162px;
    width: 1080px;
    height: 603px;
    background: linear-gradient(100deg, var(--card-mid) 0%, var(--card-light) 45%, var(--card-mid) 100%);
    box-shadow: 0 12px 30px rgba(0,0,0,.18);
    overflow: hidden;
    font-family: "Arimo", Arial, sans-serif;
  }
  .brand-square {
    position: absolute;
    left: 72px;
    top: 100px;
    width: 66px;
    height: 66px;
    background: var(--brand-orange);
  }
  .brand-name {
    position: absolute;
    left: 205px;
    top: 70px;
    margin: 0;
    font-family: "Oswald", "Arial Narrow", sans-serif;
    font-weight: 600;
    font-size: 52px;
    line-height: 1.2;
    color: var(--brand-purple);
    letter-spacing: 0.2px;
  }
  .brand-tagline {
    position: absolute;
    left: 206px;
    top: 139px;
    margin: 0;
    font-family: "Oswald", "Arial Narrow", sans-serif;
    font-weight: 500;
    font-size: 15px;
    letter-spacing: 4.1px;
    text-transform: uppercase;
    color: var(--brand-blue);
  }
  .holder-name {
    position: absolute;
    left: 72px;
    top: 236px;
    margin: 0;
    font-weight: 700;
    font-size: 37px;
    color: var(--brand-blue);
  }
  .holder-title {
    position: absolute;
    left: 73px;
    top: 283px;
    margin: 0;
    font-size: 27px;
    color: var(--ink);
  }
  .contact-band {
    position: absolute;
    left: 0;
    top: 364px;
    width: 873px;
    height: 193px;
  }
  .contact-list {
    position: absolute;
    left: 72px;
    top: 381px;
    margin: 0;
    padding: 0;
    list-style: none;
    font-size: 28px;
    color: var(--band-text);
  }
  .contact-list li {
    display: flex;
    align-items: center;
    height: 38px;
  }
  .contact-list svg {
    width: 24px;
    height: 24px;
    margin-right: 18px;
    fill: none;
    stroke: var(--band-text);
    stroke-width: 1.6;
  }
  .contact-list .phone-icon { fill: var(--band-text); stroke: none; }
  .contact-list .web { color: var(--band-muted); }
  .contact-address {
    position: absolute;
    left: 72px;
    top: 501px;
    margin: 0;
    font-size: 28px;
    color: var(--band-muted);
  }
</style>
</head>
<body>
  <article class="business-card">
    <div class="brand-square"></div>
    <h1 class="brand-name">Corvane Behavioral Health</h1>
    <p class="brand-tagline">Dedicated to hope, healing and recovery</p>

    <h2 class="holder-name">Marcus Hale</h2>
    <p class="holder-title">Manager</p>

    <svg class="contact-band" viewBox="0 0 873 193" preserveAspectRatio="none" aria-hidden="true">
      <defs>
        <radialGradient id="bandGlow" cx="0.8" cy="0.6" r="0.8">
          <stop offset="0" stop-color="var(--band-light)"/>
          <stop offset="1" stop-color="var(--band-dark)"/>
        </radialGradient>
      </defs>
      <polygon points="0,0 873,0 798,193 0,193" fill="url(#bandGlow)"/>
    </svg>

    <ul class="contact-list">
      <li>
        <svg viewBox="0 0 24 24" class="phone-icon"><path d="M6.6 10.8a15 15 0 0 0 6.6 6.6l2.2-2.2a1 1 0 0 1 1-.25 11.4 11.4 0 0 0 3.6.57 1 1 0 0 1 1 1V20a1 1 0 0 1-1 1A17 17 0 0 1 3 4a1 1 0 0 1 1-1h3.5a1 1 0 0 1 1 1c0 1.25.2 2.45.57 3.57a1 1 0 0 1-.25 1z"/></svg>
        123-456-2100
      </li>
      <li>
        <svg viewBox="0 0 24 24"><rect x="2.5" y="5.5" width="19" height="13" rx="1.5"/><path d="M3 6.5l9 6.5 9-6.5"/></svg>
        youremail@mailbox.com
      </li>
      <li class="web">
        <svg viewBox="0 0 24 24" style="stroke: var(--band-muted)"><circle cx="12" cy="12" r="9.5"/><ellipse cx="12" cy="12" rx="4.5" ry="9.5"/><path d="M2.5 12h19M4 7h16M4 17h16"/></svg>
        www.yourwebsite.com
      </li>
    </ul>
    <p class="contact-address">Your address, city, state, ZIP 0000</p>
  </article>
</body>
</html>
```